BOLD & MINIMALIST DESIGN NEEDED

We want a very bold but minimalistic business card design that is impactful and utilizes both sides of the business card. Our current logo is included for your use.

We want bold fonts and good use of negative space. We don't want the logo to overpower the design.

Target Market(s)

Professionals who are building new commercial buildings.

Industry/Entity Type

Construction

Contact Information for Business Card

Name, Title, email, office phone, cell phone, website

Font styles to use
Serif
Sans Serif

Requirements
Must have
• Bold design!

```html
<!DOCTYPE html>
<html lang="en">
<head>
<meta charset="utf-8">
<title>Ridgeline Design + Build — Business Card</title>
<link rel="stylesheet" href="https://fonts.googleapis.com/css2?family=Montserrat:wght@400;500;700;800&display=swap">
<style>
  :root {
    --backdrop: #d8d3cb;
    --card-base: #efedea;
    --green-light: #80ba3e;
    --green-dark: #5f9b2b;
    --ink: #1d1d1d;
    --panel-text: #eef3e2;
    --accent: #6fae33;
  }
  html, body {
    margin: 0;
    padding: 0;
    width: 1200px;
    height: 1047px;
    overflow: hidden;
    background: var(--backdrop);
    font-family: "Montserrat", sans-serif;
  }
  .card {
    position: absolute;
    left: 120px;
    top: 263px;
    width: 960px;
    height: 520px;
    border-radius: 24px;
    overflow: hidden;
    background: var(--card-base);
    box-shadow: 0 10px 30px rgba(0,0,0,0.12);
  }
  .card-shapes {
    position: absolute;
    inset: 0;
  }
  .brand {
    position: absolute;
    left: 44px;
    top: 150px;
    width: 420px;
    display: flex;
    align-items: center;
    gap: 16px;
    color: var(--ink);
    font-weight: 800;
  }
  .brand-square {
    width: 54px;
    height: 54px;
    background: var(--accent);
    flex: none;
  }
  .brand-name {
    line-height: 1.05;
  }
  .brand-name .line-main {
    display: block;
    font-size: 46px;
    letter-spacing: 1px;
  }
  .brand-name .line-sub {
    display: block;
    font-size: 19px;
    letter-spacing: 6px;
    margin-top: 6px;
  }
  .contact {
    position: absolute;
    right: 38px;
    top: 140px;
    text-align: right;
    color: var(--panel-text);
  }
  .contact-name {
    margin: 0;
    font-size: 36px;
    font-weight: 700;
    letter-spacing: 1.5px;
  }
  .contact-title {
    margin: 6px 0 0;
    font-size: 20px;
    font-weight: 400;
    letter-spacing: 1px;
  }
  .contact-address {
    margin: 30px 0 0;
    font-size: 22px;
    line-height: 36px;
    font-style: normal;
  }
  .contact-list {
    list-style: none;
    margin: 22px 0 0;
    padding: 0;
    font-size: 22px;
    line-height: 36px;
  }
  .contact-list li {
    display: flex;
    justify-content: flex-end;
    align-items: center;
    gap: 12px;
  }
  .contact-icon {
    width: 22px;
    height: 22px;
    flex: none;
  }
</style>
</head>
<body>
  <div class="card">
    <svg class="card-shapes" viewBox="0 0 960 520" width="960" height="520" aria-hidden="true">
      <defs>
        <linearGradient id="panelGreen" x1="0" y1="0" x2="1" y2="1">
          <stop offset="0" stop-color="var(--green-light)"/>
          <stop offset="1" stop-color="var(--green-dark)"/>
        </linearGradient>
      </defs>
      <path class="swoosh-line" fill="var(--ink)"
            d="M596 0 C628 40 616 110 560 172 C500 236 400 296 350 356 C318 396 304 460 306 520 L960 520 L960 0 Z"/>
      <path class="panel-green" fill="url(#panelGreen)"
            d="M606 0 C640 40 630 110 575 175 C520 240 420 300 370 360 C340 400 322 460 322 520 L960 520 L960 0 Z"/>
    </svg>

    <div class="brand">
      <span class="brand-square"></span>
      <span class="brand-name">
        <span class="line-main">RIDGELINE</span>
        <span class="line-sub">DESIGN + BUILD</span>
      </span>
    </div>

    <div class="contact">
      <h1 class="contact-name">MARCUS HALE</h1>
      <p class="contact-title">OWNER-CEO</p>
      <address class="contact-address">Your address<br>, City State, Zip 1234</address>
      <ul class="contact-list">
        <li>123 456 789
          <svg class="contact-icon" viewBox="0 0 24 24" aria-label="Office phone"><path fill="currentColor" d="M3 9c0-3 4-5 9-5s9 2 9 5v2h-5V9H8v2H3z M6 13h12l2 7H4z"/></svg>
        </li>
        <li>123 456 789
          <svg class="contact-icon" viewBox="0 0 24 24" aria-label="Mobile phone"><rect x="7" y="2" width="10" height="20" rx="2" fill="none" stroke="currentColor" stroke-width="2"/><circle cx="12" cy="18" r="1.3" fill="currentColor"/></svg>
        </li>
        <li>info@youremail.com
          <svg class="contact-icon" viewBox="0 0 24 24" aria-label="Email"><rect x="3" y="6" width="18" height="12" fill="currentColor"/><path d="M3 6l9 7 9-7" fill="none" stroke="var(--green-dark)" stroke-width="1.5"/></svg>
        </li>
        <li>www.yourwebsite.com
          <svg class="contact-icon" viewBox="0 0 24 24" aria-label="Website"><circle cx="12" cy="12" r="9" fill="currentColor"/><path d="M3 12h18M12 3c-4 4-4 14 0 18M12 3c4 4 4 14 0 18" fill="none" stroke="var(--green-dark)" stroke-width="1.3"/></svg>
        </li>
      </ul>
    </div>
  </div>
</body>
</html>
```